Stationery Design Task - Stationary, memo and report templates for professional services company

Looking for someone to update stationary design but just as importantly come up with a template for reports and memos for use in our consulting firm. Would also like some brand use guidelines to be able to share with our whole team. We have an existing logo that we like. Need to update with a more contemporary look so that our deliverables to clients look good and professional yet stylish. This is for business to business communications. No need for envelope design. Important to have design for multiple pages, i.e. first page of a report and then 2nd page. Need to use in MS word documents so must be easy to use and replicate. Don't want something overly complex. Clean, fresh looking is best.

Industry/Entity Type

Information Technology

Font styles to use
Sans Serif

Colors
33a6d7
0792cd
85cae6
cee9f5
cedeed
85abd2
3377b5
0455a3

Requirements
Must have
• Clean look but with a little style or pop. Something that can easily be used in word documents. Need to have page styles that have a first page of a report (not a cover page) and then secondary page.
Nice to have
• - Although the dark blue is our primary color. Might be willing to look at some accent color as well.
Should not have
• Not just our logo on the page with a color bar.

```html
<!DOCTYPE html>
<html lang="en">
<head>
<meta charset="utf-8">
<title>Vantage Systems Stationery</title>
<link href="https://fonts.googleapis.com/css2?family=Roboto:wght@400;700;900&family=Questrial&display=swap" rel="stylesheet">
<style>
  :root {
    --stage: #666666;
    --brand-blue: #0792cd;
    --band-blue: #0a80c6;
    --title-grey: #6d6e70;
    --text-grey: #555555;
    --paper-light: #f4f4f4;
    --paper-mid: #e4e4e4;
    --paper-dark: #c6c6c6;
  }
  * { box-sizing: border-box; margin: 0; padding: 0; }
  html, body { width: 1200px; height: 578px; overflow: hidden; background: var(--stage); }
  .canvas { position: relative; width: 1200px; height: 578px; overflow: hidden; background: var(--stage); }

  .page {
    position: absolute; top: 52px; width: 338px; height: 475px; overflow: hidden;
    font-family: "Questrial", sans-serif; color: var(--text-grey);
  }
  .page--cover { left: 62px; background: linear-gradient(180deg, var(--paper-light) 0%, var(--paper-mid) 45%, var(--paper-dark) 100%); }
  .page--letter { left: 434px; background: linear-gradient(180deg, #ffffff 0%, #f3f3f3 55%, #dcdcdc 100%); }
  .page--back { left: 806px; background: linear-gradient(90deg, #d4d4d4 0%, #efefef 30%, #fafafa 100%); }

  .brand { position: absolute; display: flex; align-items: center; }
  .brand__dot { border-radius: 50%; background: var(--brand-blue); flex: none; }
  .brand__name { font-family: "Roboto", sans-serif; font-weight: 700; color: var(--brand-blue); white-space: nowrap; }

  .cover-brand { left: 44px; top: 86px; gap: 12px; }
  .cover-brand .brand__dot { width: 46px; height: 46px; }
  .cover-brand .brand__name { font-size: 20px; letter-spacing: 0.3px; }

  .cover-title { position: absolute; left: 0; right: 0; top: 222px; text-align: center; font-family: "Roboto", sans-serif; }
  .cover-title__main { font-size: 28px; font-weight: 700; color: var(--title-grey); line-height: 1; }
  .cover-title__sub { margin-top: 7px; font-size: 11.5px; font-weight: 700; color: var(--brand-blue); }

  .prepared { position: absolute; left: 98px; width: 140px; top: 362px; text-align: center; font-family: "Roboto", sans-serif;
    border-top: 1px solid #8a8a8a; border-bottom: 1px solid #8a8a8a; padding: 6px 0 5px; }
  .prepared__label { font-size: 11.5px; font-weight: 700; color: var(--title-grey); }
  .prepared__name { margin-top: 2px; font-size: 10.5px; color: var(--brand-blue); }

  .band { position: absolute; left: 0; right: 0; top: 445px; height: 15px; background: var(--band-blue);
    color: #ffffff; display: flex; align-items: center; font-family: "Roboto", sans-serif; }
  .band--cover { font-size: 7.6px; justify-content: space-between; padding: 0 22px; }
  .band--letter { font-size: 5.3px; font-weight: 700; justify-content: center; gap: 6px; }
  .web { position: absolute; left: 0; right: 0; top: 465px; text-align: center; font-size: 5.6px; letter-spacing: 1.4px; color: var(--brand-blue); }

  .letter-brand { left: 84px; top: 30px; gap: 8px; }
  .letter-brand .brand__dot { width: 28px; height: 28px; }
  .letter-brand .brand__name { font-size: 17px; }

  .pattern { position: absolute; border-radius: 50%; }
  .pattern--letter { left: 110px; top: 120px; width: 230px; height: 330px;
    background: radial-gradient(ellipse at 55% 50%, rgba(210,210,210,0.55) 0%, rgba(225,225,225,0.25) 55%, rgba(255,255,255,0) 72%); }
  .pattern--back { left: 40px; top: 90px; width: 290px; height: 330px;
    background: radial-gradient(ellipse at 55% 50%, rgba(205,205,205,0.6) 0%, rgba(220,220,220,0.3) 55%, rgba(255,255,255,0) 72%); }

  .letter-body { position: absolute; left: 31px; top: 132px; width: 290px; }
  .salutation { font-size: 8.2px; color: var(--text-grey); margin-bottom: 14px; }
  .letter-body p.copy { font-size: 4.4px; line-height: 6.4px; text-align: justify; margin-bottom: 11px; color: #666666; }
  .signoff { font-size: 4.4px; margin-top: 14px; color: #666666; }
  .signature { margin-top: 8px; width: 60px; height: 22px; border-radius: 11px;
    background: linear-gradient(90deg, rgba(86,120,170,0.25), rgba(86,120,170,0.08)); }

  .back-brand { left: 262px; top: 413px; gap: 4px; }
  .back-brand .brand__dot { width: 24px; height: 24px; }
  .back-brand .brand__name { font-size: 7px; }
</style>
</head>
<body>
<div class="canvas">

  <section class="page page--cover">
    <div class="brand cover-brand">
      <span class="brand__dot"></span>
      <span class="brand__name">VANTAGE SYSTEMS</span>
    </div>
    <div class="cover-title">
      <h1 class="cover-title__main">REPORT TITLE</h1>
      <p class="cover-title__sub">YOUR SUBTITLE HERE</p>
    </div>
    <div class="prepared">
      <p class="prepared__label">REPORT PREPARED BY</p>
      <p class="prepared__name">YOUR NAME HERE</p>
    </div>
    <div class="band band--cover">
      <span>PROPOSAL ISSUED : SEP 19,2018</span>
      <span>PROPOSAL VALID TO : SEP 19,2019</span>
    </div>
  </section>

  <section class="page page--letter">
    <div class="pattern pattern--letter" role="img" aria-label="Faint decorative hexagon pattern"></div>
    <div class="brand letter-brand">
      <span class="brand__dot"></span>
      <span class="brand__name">VANTAGE SYSTEMS</span>
    </div>
    <div class="letter-body">
      <p class="salutation">Dear Mr. Carter,</p>
      <p class="copy">Thank you for meeting with our team last week to discuss the upgrade of your regional network. As agreed, we have prepared a short summary of the scope, the schedule and the resources required for each phase of the work. Our engineers reviewed the current systems on site and noted several areas where performance and security can be improved at modest cost. We expect the first phase to begin early next quarter.</p>
      <p class="copy">The proposal attached to this letter sets out each task in detail, together with the staff assigned and the hours we estimate for it. Where your own team can take on part of the work, we have marked the task so that costs can be reduced. All figures are fixed for ninety days from the date of issue and include travel, testing and final handover.</p>
      <p class="copy">During the project a single lead consultant will remain your contact and will send a brief status report every Friday. Any change to the scope will be agreed in writing before work continues. Once the systems are live, we will provide training for your staff and a full set of documents describing the new setup.</p>
      <p class="copy">Please review the enclosed pages at your convenience and let us know of any questions. We look forward to working with you and your team on this project.</p>
      <p class="signoff">Sincerely,</p>
      <div class="signature" role="img" aria-label="Handwritten signature of Daniel Reyes"></div>
    </div>
    <div class="band band--letter">
      <span>214 HARBOR POINT ROAD, KENMORE, OREGON 97120</span>
      <span>555 210 4476 | HELLO@VANTAGESYSTEMS.EXAMPLE</span>
    </div>
    <p class="web">www.vantagesystems.example</p>
  </section>

  <section class="page page--back">
    <div class="pattern pattern--back" role="img" aria-label="Faint decorative hexagon pattern"></div>
    <div class="brand back-brand">
      <span class="brand__name">VANTAGE</span>
      <span class="brand__dot"></span>
    </div>
  </section>

</div>
</body>
</html>
```